Letterhead and matching envelope design for a dental office

We need a new stationary design, letterhead and envelope #10, for a dental office in Denver area. We are called Bright Harbor Dental. We want a simple and minimalistic design but not a boring design. I wish to have one good point that makes it look professional. I have attached our logo. Feel free to use either one. I want the design for letterhead and envelope look like a "matching pair" but not look the same. The envelope doesn't have to be white and it will have an address window on bottom left.

Target Market(s)

everyone who visits dentist (adults)

Industry/Entity Type

Dental

Font styles to use
Other font styles liked:
• close to font on logo or something that matches well

Requirements
Must have
• professional
• simple, minimalistic
• unique point that stands out
Nice to have
• matching but not same design for letterhead and envelope
Should not have
• not look like all the other boring designs
• no flowery, distracting feats

```html
<!DOCTYPE html>
<html lang="en">
<head>
<meta charset="utf-8">
<title>Bright Harbor Dental – Letterhead</title>
<link rel="stylesheet" href="https://fonts.googleapis.com/css2?family=Source+Sans+3:wght@400;600&family=Caveat:wght@500&display=swap">
<style>
  :root {
    --green: #3bb44a;
    --green-mid: #a9d9ae;
    --green-pale: #d9efdb;
    --ink: #3a3a3a;
    --signature: #2b2f8f;
    --paper: #ffffff;
    --backdrop: #e8e8e5;
  }
  * { margin: 0; padding: 0; box-sizing: border-box; }
  html, body {
    width: 953px; height: 1200px; overflow: hidden;
    background: var(--backdrop);
    font-family: "Source Sans 3", "Myriad Pro", sans-serif;
    color: var(--ink);
  }
  .letterhead {
    position: absolute; left: 160px; top: 155px;
    width: 639px; height: 905px;
    background: var(--paper);
    box-shadow: 0 2px 10px rgba(0,0,0,.12);
  }
  .header-wave { position: absolute; left: 0; top: 0; width: 639px; height: 110px; }
  .address {
    position: absolute; right: 38px; top: 21px;
    text-align: right; color: #fff; font-size: 14px; line-height: 19px;
  }
  .brand {
    position: absolute; left: 36px; top: 118px;
    display: flex; align-items: center; gap: 8px;
    color: var(--green); font-size: 17px; font-weight: 600; line-height: 20px;
    width: 150px;
  }
  .brand-dot {
    flex: none; width: 14px; height: 14px; border-radius: 50%;
    background: var(--green);
  }
  .letter {
    position: absolute; left: 36px; top: 316px; width: 565px;
    font-size: 13.2px; line-height: 16.6px;
  }
  .letter-date { font-size: 14px; margin-bottom: 4px; }
  .letter p { text-align: justify; margin-bottom: 16.6px; }
  .signature {
    position: absolute; left: 36px; top: 652px;
  }
  .signature-name {
    font-family: "Caveat", cursive; font-size: 30px; line-height: 32px;
    color: var(--signature);
  }
  .signature-role { font-size: 14px; margin-top: 2px; }
  .footer-rule {
    position: absolute; left: 40px; right: 40px; top: 854px; height: 1px;
    background: linear-gradient(90deg, transparent, var(--green-mid) 20%, var(--green-mid) 80%, transparent);
  }
  .contacts {
    position: absolute; left: 0; right: 0; top: 870px;
    display: flex; justify-content: center; gap: 6px;
    font-size: 12px; line-height: 14px;
  }
  .contact { display: flex; align-items: center; gap: 4px; }
  .contact-icon { width: 11px; height: 11px; }
</style>
</head>
<body>
  <main class="letterhead">
    <svg class="header-wave" viewBox="0 0 639 110" aria-hidden="true">
      <path d="M0,22 C120,8 260,30 380,60 C470,82 560,98 639,100 V104 C540,104 430,88 330,68 C210,44 100,40 0,82 Z" fill="var(--green-pale)"/>
      <path d="M0,20 C110,4 250,22 370,52 C470,78 560,94 639,96 V100 C550,100 440,82 340,58 C220,32 100,22 0,48 Z" fill="var(--green-mid)"/>
      <path d="M0,0 H639 V92 C560,92 470,76 380,52 C260,20 120,0 0,14 Z" fill="var(--green)"/>
      <path d="M0,15 C120,1 260,21 380,53 C470,77 560,93 639,93" fill="none" stroke="#fff" stroke-width="2.2"/>
    </svg>
    <div class="address">2715 Linden Crest Blvd,<br>Suite 210 Arvada, Co 80004</div>

    <div class="brand"><span class="brand-dot"></span><span>Bright Harbor Dental</span></div>

    <section class="letter">
      <div class="letter-date">Lakewood January, 2016</div>
      <p>Lorem Ipsum is simply dummy text of the printing and typesetting industry. Lorem Ipsum has been the industry's standard dummy text ever since the 1500s, when an unknown printer took a galley of type and scrambled it to make a type specimen book. It has survived not only five centuries, but also the leap into electronic typesetting, remaining essentially unchanged. It was popularised in the 1960s with the release of Linoset sheets containing Lorem Ipsum passages, and more recently with desktop publishing software like Quillset Layout including versions of Lorem Ipsum.</p>
      <p>The standard chunk of Lorem Ipsum used since the 1500s is reproduced below for those interested. Sections 1.10.32 and 1.10.33 from "de Finibus Bonorum et Malorum" by Marcus Tellan are also reproduced in their exact original form, accompanied by English versions from the 1914 translation by H. Dunmore</p>
      <p>Lorem Ipsum is simply dummy text of the printing and typesetting industry. Lorem Ipsum has been the industry's standard dummy text ever since the 1500s, when an unknown printer took a galley of type and scrambled it to make a type specimen book. It has survived not only five centuries, but also the leap into electronic typesetting, remaining essentially unchanged. It was popularised in the</p>
    </section>

    <div class="signature">
      <div class="signature-name">your name</div>
      <div class="signature-role">Company Director</div>
    </div>

    <div class="footer-rule"></div>
    <footer class="contacts">
      <span class="contact">
        <svg class="contact-icon" viewBox="0 0 12 12" aria-hidden="true"><circle cx="6" cy="6" r="6" fill="var(--green)"/><path d="M4,3 L5,3.2 L5.4,4.6 L4.8,5.2 C5.2,6 5.9,6.7 6.8,7.2 L7.4,6.6 L8.8,7 L9,8 C8.4,8.8 7.6,9 6.6,8.6 C5,7.9 4,6.8 3.4,5.2 C3.1,4.3 3.3,3.5 4,3 Z" fill="#fff"/></svg>
        303-555-0147
      </span>
      <span class="contact">
        <svg class="contact-icon" viewBox="0 0 12 12" aria-hidden="true"><circle cx="6" cy="6" r="6" fill="var(--green)"/><rect x="3" y="4" width="6" height="4" fill="none" stroke="#fff" stroke-width="1"/><path d="M3,4 L6,6.3 L9,4" fill="none" stroke="#fff" stroke-width="1"/></svg>
        info@brightharbordental.com
      </span>
      <span class="contact">
        <svg class="contact-icon" viewBox="0 0 12 12" aria-hidden="true"><circle cx="6" cy="6" r="6" fill="var(--green)"/><circle cx="6" cy="6" r="3.2" fill="none" stroke="#fff" stroke-width="0.9"/><path d="M2.8,6 H9.2 M6,2.8 C4.6,4.6 4.6,7.4 6,9.2 M6,2.8 C7.4,4.6 7.4,7.4 6,9.2" fill="none" stroke="#fff" stroke-width="0.7"/></svg>
        www.brightharbordental.com
      </span>
    </footer>
  </main>
</body>
</html>
```